Vetern Mailer for Mortgage Refinance

Hello, I need some options in my KB mailers we send out here in the USA! A sample of our mailer has been included. I need all the verbiage the same. The data merge points need to stay on too. Please make this pop. We have a high end PELDO printer and a Z auto folding machine. Letter goes into a number 10 envelope with windows. So lets see what you can do. One with colors below is our company colors and then one black, white, gray.
Blue - 3399FF------ R 51 G 153 B 255
Orange - FF9933----- R 255 G 153 B 51
Black – 333333------ R 51 G 51 B 51
White – FFFFFF------ R 255 G 255 B 255

Target Market(s)

United States Military Service Members

Industry/Entity Type

Mortgage Lender

Requirements
Must have
• Margins for folding with Z and Number 10 Envelope with two windows

```html
<!DOCTYPE html>
<html lang="en">
<head>
<meta charset="utf-8">
<title>Summit Crest Home Loans – KB IRRRL Mailer</title>
<link href="https://fonts.googleapis.com/css2?family=Montserrat:wght@300;400;500;600;700;800&display=swap" rel="stylesheet">
<style>
:root{
  --blue:#3399ff;
  --blue-deep:#1f86f0;
  --orange:#ff9933;
  --ink:#333333;
  --white:#ffffff;
  --canvas:#eef1f4;
  --muted:#555b63;
}
*{box-sizing:border-box;margin:0;padding:0}
html,body{width:1200px;height:4000px;overflow:hidden}
body{background:var(--canvas);font-family:"Montserrat",Arial,sans-serif;color:var(--ink)}
.sheet{position:absolute;left:80px;width:1040px;height:1350px;box-shadow:0 6px 24px rgba(0,0,0,.18);overflow:hidden}
.sheet--front{top:100px;background:var(--blue)}
.sheet--back{top:1560px;background:var(--blue);padding:30px 30px 0}
.merge{font-weight:700}
.merge-blue{color:var(--blue);font-weight:600}

/* front: top panel */
.address-panel{position:relative;height:440px;background:var(--white);border-radius:0 0 56px 56px;padding:58px 62px 0}
.re-line{font-size:15px;font-weight:700;line-height:1.35}
.re-line .label{color:var(--blue)}
.notice{font-size:12.5px;margin-top:16px;width:560px;line-height:1.35}
.recipient{margin-top:22px;font-size:15px;font-weight:700;line-height:1.35}
.skip-box{position:absolute;right:62px;top:52px;width:196px}
.skip-box__badge{background:var(--orange);color:var(--white);border-radius:6px;text-align:center;padding:10px 8px 8px}
.skip-box__months{font-size:13px;font-weight:600;line-height:1.25}
.skip-box__amount{font-size:38px;font-weight:800;line-height:1.1}
.skip-box__note{font-size:12.5px;text-align:center;line-height:1.35;margin-top:8px}
.salutation{margin-top:28px;font-size:16px;font-weight:700;color:var(--blue)}
.intro{margin-top:14px;font-size:13px;line-height:1.35;color:var(--muted)}
.intro .amt{color:var(--orange);font-weight:700}

/* front: benefits band */
.benefits{height:465px;padding:62px 62px 0;color:var(--white)}
.benefits__title{text-align:center;font-size:21px;font-weight:600;letter-spacing:.3px}
.benefits__cols{display:flex;gap:60px;margin-top:28px;padding-left:22px}
.benefit-col{flex:1}
.pill{display:inline-block;background:var(--orange);color:var(--white);font-size:22px;font-weight:600;padding:6px 18px;border-radius:6px}
.benefit-list{list-style:none;margin-top:22px}
.benefit-list li{display:flex;align-items:center;gap:12px;font-size:15.5px;font-weight:500;height:42px}
.benefit-list svg{flex:0 0 24px}

/* front: call panel */
.call-panel{height:445px;background:var(--white);border-radius:56px 56px 0 0;padding:46px 58px 0;text-align:center}
.call-text{font-size:15px;line-height:1.35;color:var(--muted)}
.brand{margin-top:22px;display:flex;justify-content:center;align-items:center;gap:14px}
.brand__mark{width:18px;height:18px;background:var(--orange);border-radius:50%}
.brand__name{font-size:50px;font-weight:300;letter-spacing:6px;color:var(--blue)}
.contact-line{font-size:15px;font-weight:700;margin-top:12px;line-height:1.45}
.cash-out{display:inline-flex;margin-top:10px;font-size:18px;font-weight:600;border-radius:4px;overflow:hidden}
.cash-out__label{background:var(--orange);color:var(--ink);padding:6px 14px}
.cash-out__value{background:var(--blue);color:var(--white);padding:6px 16px}
.info-row{display:flex;gap:14px;justify-content:center;margin-top:24px}
.info-row span{border:2px solid var(--blue);border-radius:6px;padding:10px 16px;font-size:14px;font-weight:600}
.info-row .w1{width:262px}.info-row .w2{width:200px}.info-row .w3{width:458px}
.reverse-note{margin-top:14px;font-size:13.5px;font-weight:600}

/* back */
.back-card{background:var(--white);border-radius:40px 40px 0 0;height:1320px;padding:450px 36px 0}
.fine{font-size:10.2px;line-height:1.3;color:var(--muted);margin-bottom:16px}
.points{list-style:none;margin-bottom:16px}
.points li{display:flex;gap:10px;font-size:10.2px;line-height:1.3;color:var(--muted);margin-bottom:12px}
.points .num{flex:0 0 22px;height:22px;border-radius:50%;background:var(--orange);color:var(--white);font-size:10px;font-weight:700;display:flex;align-items:center;justify-content:center}
</style>
</head>
<body>

<section class="sheet sheet--front">
  <header class="address-panel">
    <p class="re-line"><span class="label">RE:</span> &lt;&lt;lender&gt;&gt;<br><span class="label">Loan ID Number:</span> &lt;&lt;loan_id&gt;&gt;</p>
    <p class="notice">Summit Crest Home Loans LLC is not affiliated with your current lender nor is it an agency of the Federal Government</p>
    <p class="recipient">&lt;&lt;first_name&gt;&gt; &lt;&lt;last_name&gt;&gt;<br>&lt;&lt;address&gt;&gt;<br>&lt;&lt;city_state_zip&gt;&gt;</p>

    <aside class="skip-box">
      <div class="skip-box__badge">
        <div class="skip-box__months">&lt;&lt;close_month&gt;&gt; &amp;<br>&lt;&lt;skip_month&gt;&gt;</div>
        <div class="skip-box__amount">$0</div>
      </div>
      <p class="skip-box__note">You may be able to defer<br>your next two payments.<sup>1</sup><br>Call toll-free <span class="merge">&lt;&lt;phone_number&gt;&gt;</span><br>Weekdays 6 a.m. to 5 p.m. PST</p>
    </aside>

    <p class="salutation">Dear &lt;&lt;first_name&gt;&gt;</p>
    <p class="intro">We are contacting you regarding your &lt;&lt;balance&gt;&gt; KB loan. Our review has indicated that because of homes appreciating in &lt;&lt;city&gt;&gt;, you may now qualify for additional benefits. These benefits may include lowering your monthly mortgage payment, deferring up to two pay-ments, refund of escrow, and <span class="amt">$35,000</span> or more cash-out.3 Call our KB Program Specialist at &lt;&lt;phone_number&gt;&gt; at your earliest convenience to receive a detailed explanation of how you may be able to access these benefits</p>
  </header>

  <section class="benefits">
    <h2 class="benefits__title">YOU MAY ALSO RECEIVE A CHECK BACK FROM YOUR ESCROW ACCOUNT.</h2>
    <div class="benefits__cols">
      <div class="benefit-col">
        <span class="pill">ADDITIONAL BENEFITS INCLUDE:</span>
        <ul class="benefit-list">
          <li><svg width="24" height="24" viewBox="0 0 24 24"><rect width="24" height="24" rx="5" fill="#fff"/><rect x="3" y="3" width="18" height="18" rx="4" fill="#ff9933"/><path d="M7 12.5l3 3 7-7" stroke="#fff" stroke-width="2.4" fill="none"/></svg>100% LTV Cash-Out Available</li>
          <li><svg width="24" height="24" viewBox="0 0 24 24"><rect width="24" height="24" rx="5" fill="#fff"/><rect x="3" y="3" width="18" height="18" rx="4" fill="#ff9933"/><path d="M7 12.5l3 3 7-7" stroke="#fff" stroke-width="2.4" fill="none"/></svg>Pay off High Interest Debt</li>
          <li><svg width="24" height="24" viewBox="0 0 24 24"><rect width="24" height="24" rx="5" fill="#fff"/><rect x="3" y="3" width="18" height="18" rx="4" fill="#ff9933"/><path d="M7 12.5l3 3 7-7" stroke="#fff" stroke-width="2.4" fill="none"/></svg>Complete a long overdue home renovation</li>
          <li><svg width="24" height="24" viewBox="0 0 24 24"><rect width="24" height="24" rx="5" fill="#fff"/><rect x="3" y="3" width="18" height="18" rx="4" fill="#ff9933"/><path d="M7 12.5l3 3 7-7" stroke="#fff" stroke-width="2.4" fill="none"/></svg>No out-of-pocket appraisal deposit</li>
          <li><svg width="24" height="24" viewBox="0 0 24 24"><rect width="24" height="24" rx="5" fill="#fff"/><rect x="3" y="3" width="18" height="18" rx="4" fill="#ff9933"/><path d="M7 12.5l3 3 7-7" stroke="#fff" stroke-width="2.4" fill="none"/></svg>No Private Mortgage Insurance</li>
        </ul>
      </div>
      <div class="benefit-col">
        <span class="pill">KB IRRRL Benefits:</span>
        <ul class="benefit-list">
          <li><svg width="24" height="24" viewBox="0 0 24 24"><rect width="24" height="24" rx="5" fill="#fff"/><rect x="3" y="3" width="18" height="18" rx="4" fill="#ff9933"/><path d="M7 12.5l3 3 7-7" stroke="#fff" stroke-width="2.4" fill="none"/></svg>Reduce Your Current Interest Rate</li>
          <li><svg width="24" height="24" viewBox="0 0 24 24"><rect width="24" height="24" rx="5" fill="#fff"/><rect x="3" y="3" width="18" height="18" rx="4" fill="#ff9933"/><path d="M7 12.5l3 3 7-7" stroke="#fff" stroke-width="2.4" fill="none"/></svg>Mortgage-Only Credit Report</li>
          <li><svg width="24" height="24" viewBox="0 0 24 24"><rect width="24" height="24" rx="5" fill="#fff"/><rect x="3" y="3" width="18" height="18" rx="4" fill="#ff9933"/><path d="M7 12.5l3 3 7-7" stroke="#fff" stroke-width="2.4" fill="none"/></svg>No Appraisal Required</li>
          <li><svg width="24" height="24" viewBox="0 0 24 24"><rect width="24" height="24" rx="5" fill="#fff"/><rect x="3" y="3" width="18" height="18" rx="4" fill="#ff9933"/><path d="M7 12.5l3 3 7-7" stroke="#fff" stroke-width="2.4" fill="none"/></svg>Fast Closings in 8-14 days</li>
          <li><svg width="24" height="24" viewBox="0 0 24 24"><rect width="24" height="24" rx="5" fill="#fff"/><rect x="3" y="3" width="18" height="18" rx="4" fill="#ff9933"/><path d="M7 12.5l3 3 7-7" stroke="#fff" stroke-width="2.4" fill="none"/></svg>No Income or Asset Verification Required</li>
        </ul>
      </div>
    </div>
  </section>

  <footer class="call-panel">
    <p class="call-text">We recommend you call our office at <span class="merge" style="color:var(--ink)">&lt;&lt;phone_number&gt;&gt;</span> within the next 3-5 business days as market rates fluctuate. By taking action now your next mortgage payment may not be due until &lt;&lt;next_pay_month&gt;&gt;.<sup>2</sup> To avoid further delay, please call today.</p>
    <div class="brand"><span class="brand__mark"></span><span class="brand__name">SUMMIT CREST</span></div>
    <p class="contact-line">Phone : <span class="merge-blue">&lt;&lt;phone_number&gt;&gt;</span><br>Loan ID Number: <span class="merge-blue">&lt;&lt;loan_id&gt;&gt;</span></p>
    <div class="cash-out"><span class="cash-out__label">Cash Out Options (Tax Free):</span><span class="cash-out__value">$35,000 or more</span></div>
    <div class="info-row"><span class="w1">Summit Crest Home Loans LLC</span><span class="w2">NMLS 4820163</span><span class="w3">2200 N Mesa Ridge Rd Ste 140 Phoenix, AZ 85016</span></div>
    <p class="reverse-note">*Please see reverse for disclaimer</p>
  </footer>
</section>

<section class="sheet sheet--back">
  <div class="back-card">
    <p class="fine">Offer is available only for loans made or arranged through Summit Crest Home Loans LLC, NMLS# 4820163, 2200 N Mesa Ridge Rd, Ste 140, Phoenix, AZ 85016, which is not associated with, or acting on behalf of, your current lender or any government agency. Verification of employment may apply. This program is exclusive to the beneficiary named above and is nontransferable.</p>
    <p class="fine">TERMS AND CONDITIONS: This offer is extended because you appear to satisfy certain credit criteria drawn from information in a prescreened report received from a consumer reporting agency used by us. The amount and terms of any credit offer we extend to you will be set by your credit history, your ability to repay and the available equity in your home. The minimum loan amount shall be no less than $50,000.00. You may no longer qualify if you do not continue to meet the criteria used to select you or if you are unable to furnish any required collateral. To qualify you may be required to provide up to two years of income verification. This offer is not an approval. Your debt-to-income ratio may not exceed 50%; other programs may be available with a higher ratio. Credit severity may affect down payment. The lender may cancel this offer if it cannot verify the information you provided. All bankruptcies must be discharged. The lender or an affiliated lender must be in a valid first or second lien position and property hazard insurance is required. Additional information and documentation may be needed to issue a loan commitment. The amount of the cash-out offered is based on the current balance that is reported by one of the three national credit bureaus.</p>
    <p class="fine">State Disclosure Requirements: Summit Crest Home Loans LLC is a licensed mortgage lender/broker. The states listed below require disclosure of licensing information. (If your state is not listed, it does not require a specific license disclosure.)</p>
    <p class="fine">AZ Department of Insurance and Financial Institutions License #: 0000000 &amp; 4820163, CA Licensed by the Department of Financial Protection and Innovation under the California Residential Mortgage Lending Act, License #: 00000-000000 &amp; 4820163, CO Department of Regulatory Agencies License #: 4820163, FL Office of Financial Regulation License #: MLD0000 &amp; 4820163, ID Mortgage Broker/Lender License #: MBL-0000000 &amp; 4820163, MT Banking &amp; Financial Institutions License #: 4820163, OR Division of Financial Regulation License #: 4820163, TN Department of Financial Institutions #: 4820163, TX SML Mortgage Company License #: 4820163, UT Department of Commerce License #: 00000000 &amp; 4820163, WA Department of Financial Institutions License #: CL-4820163.</p>
    <ol class="points">
      <li><span class="num">01</span><span>Deferred mortgage payments: If you do not make your mortgage payment for the month that you are closing your new loan, it may be possible to capitalize that payment into your new loan, moving the due date of your next payment out one to two months. Please be aware that deferring your payment as described may result in additional interest charges over the life of your loan. The deferred interest will be added to the principal balance of your new loan, which may increase your future monthly payments and the total amount paid over the term. It is important to understand these implications before deciding. While your mortgage payment is not considered officially late on your credit until 30 days past the due date, late fees may apply if payment is not received within 15 days of the due date. Please manage your payments responsibly to avoid extra charges and to keep a healthy credit status.</span></li>
      <li><span class="num">02</span><span>Escrow Account Refund (if applicable): If you have an escrow account associated with your mortgage, please be aware that any refund from this account is governed by the terms and conditions of your current lender. The timing and amount of a potential refund depend on the balance at the time of loan payoff and specific escrow requirements. For those without an escrow account, this clause does not apply. We advise all borrowers to contact their current lender for detailed information about their escrow status and refund eligibility.</span></li>
      <li><span class="num">03</span><span>Example cash-out of $35,000 will be in addition to your monthly mortgage payment. Cash-out offer assumes you have adequate equity in your property. A full appraisal will be required with your loan application to determine the actual value. Your actual rate and payment may differ based on many factors. Please contact one of our licensed Lending Officers at 855-555-0147 for a customized rate and payment quote. Cash-out offers may not be available in TX.</span></li>
      <li><span class="num">04</span><span>Your circumstances may vary, so please contact 855-555-0147 to see how we may assist.</span></li>
    </ol>
    <p class="fine">Summit Crest Home Loans is an Equal Housing Lender. As prohibited by federal law, we do not engage in business practices that discriminate on the basis of race, color, religion, national origin, sex, marital status, age (provided you have the capacity to enter into a binding contract), because all or part of your income may be derived from any public assistance program, or because you have, in good faith, exercised any right under the Consumer Credit Protection Act. The federal agency that administers our compliance with these federal laws is the Federal Trade Commission, Equal Credit Opportunity, Washington, DC 20580.</p>
  </div>
</section>

</body>
</html>
```